Irrigation Business needs their business cards modernised and revamped

I would like to keep my current logo, colours and revamp the format of the card.

I would like the card to be clean yet important.

Im not sure if you include texture but i would like the named logo to be indented into the card etc.

show me something alive and free something thats clinical to the point yet has a feel of achievement. i would like people to go nice card.

Target Market(s)

high end clients, corporate, sports field manger, the guys that make the decisions

Industry/Entity Type

Business

Contact Information for Business Card

nformation to be included

Dean Harlow (Director)
0487305526
dean@kolvat.biz
www.kestonfieldworks.com

instagram logo
google logo
facebook logo

Colors

Designer to choose colors to be used in the design.

Requirements
Nice to have
• indentations a really nice feel to the card good texture

```html
<!DOCTYPE html>
<html lang="en">
<head>
<meta charset="utf-8">
<title>Keston Fieldworks – Business Card</title>
<link rel="stylesheet" href="https://fonts.googleapis.com/css2?family=Lato:wght@400;700;900&display=swap">
<style>
  :root {
    --backdrop: #1c1c1d;
    --paper: #f4f4f2;
    --sky: #2a9ed1;
    --deep: #2f6db5;
    --ink: #2c5ea8;
    --white: #ffffff;
  }
  * { margin: 0; padding: 0; box-sizing: border-box; }
  html, body {
    width: 960px; height: 1200px; overflow: hidden;
    background: var(--backdrop);
    font-family: "Lato", sans-serif;
  }
  .card {
    position: absolute; left: 100px;
    width: 760px; height: 434px;
    border-radius: 28px; overflow: hidden;
    background: var(--paper);
  }
  .card--front { top: 110px; }
  .card--back { top: 656px; }

  .band { position: absolute; left: 0; width: 100%; }
  .band--sky { background: var(--sky); height: 64px; }
  .band--deep { background: var(--deep); top: 374px; height: 60px; }
  .band--1 { top: 150px; }
  .band--2 { top: 224px; }
  .band--3 { top: 298px; }

  .holder-name {
    position: absolute; right: 44px; top: 70px;
    color: var(--ink); font-size: 29px; letter-spacing: 0.5px;
  }
  .holder-name strong { font-weight: 900; }
  .holder-name .role { font-weight: 400; }

  .contact {
    position: absolute; left: 372px;
    display: flex; align-items: center; gap: 16px;
    color: var(--white); font-size: 22px; letter-spacing: 0.6px;
  }
  .contact--phone { top: 165px; }
  .contact--mail { top: 239px; }
  .contact--web { top: 313px; }
  .contact .icon {
    width: 32px; height: 32px; border-radius: 50%;
    background: var(--white);
    display: flex; align-items: center; justify-content: center;
  }

  .brand-disc {
    position: absolute; left: 78px; top: 138px;
    width: 230px; height: 230px; border-radius: 50%;
    background: var(--white);
    display: flex; align-items: center; justify-content: center;
    text-align: center;
  }
  .brand-disc .brand-name {
    color: var(--ink); font-weight: 900; font-size: 25px; line-height: 1.15;
    letter-spacing: 1px;
  }

  .back-lockup {
    position: absolute; left: 0; top: 84px; width: 100%;
    display: flex; flex-direction: column; align-items: center;
  }
  .back-lockup .brand-dot {
    width: 112px; height: 112px; border-radius: 50%;
    background: var(--sky);
  }
  .back-lockup .brand-name {
    margin-top: 22px;
    color: var(--ink); font-weight: 900; font-size: 40px; letter-spacing: 1px;
  }
  .social-row {
    margin-top: 30px; display: flex; gap: 22px;
  }
  .social-row .social-slot {
    width: 44px; height: 44px; border-radius: 50%;
    border: 2.5px solid var(--ink);
  }
</style>
</head>
<body>

<section class="card card--front">
  <div class="band band--sky band--1"></div>
  <div class="band band--sky band--2"></div>
  <div class="band band--sky band--3"></div>
  <div class="band band--deep"></div>

  <p class="holder-name"><strong>DEAN HARLOW</strong> <span class="role">| Director</span></p>

  <div class="brand-disc">
    <span class="brand-name">KESTON<br>FIELDWORKS</span>
  </div>

  <div class="contact contact--phone">
    <span class="icon">
      <svg width="14" height="18" viewBox="0 0 14 18"><rect x="1.5" y="1" width="11" height="16" rx="2" fill="none" stroke="#2a9ed1" stroke-width="2"/><circle cx="7" cy="14" r="1.2" fill="#2a9ed1"/></svg>
    </span>
    <span>0487305526</span>
  </div>
  <div class="contact contact--mail">
    <span class="icon">
      <svg width="18" height="13" viewBox="0 0 18 13"><rect x="1" y="1" width="16" height="11" fill="#2a9ed1"/><path d="M1 1 L9 7 L17 1" fill="none" stroke="#fff" stroke-width="1.5"/></svg>
    </span>
    <span>dean@kolvat.biz</span>
  </div>
  <div class="contact contact--web">
    <span class="icon">
      <svg width="20" height="20" viewBox="0 0 20 20" fill="none" stroke="#2a9ed1" stroke-width="1.5"><circle cx="10" cy="10" r="8"/><ellipse cx="10" cy="10" rx="3.5" ry="8"/><path d="M2 10 H18 M3.5 6 H16.5 M3.5 14 H16.5"/></svg>
    </span>
    <span>www.kestonfieldworks.com</span>
  </div>
</section>

<section class="card card--back">
  <div class="back-lockup">
    <div class="brand-dot"></div>
    <p class="brand-name">KESTON FIELDWORKS</p>
    <div class="social-row">
      <span class="social-slot"></span>
      <span class="social-slot"></span>
      <span class="social-slot"></span>
    </div>
  </div>
</section>

</body>
</html>
```